Catalogue Design Project

We need a catalog design for a new private university called Redwell Institute Bayshore (see website www.rwi-bs.org). The catalog should be about 30 pages maximum and will include items such as General Information, Academic schedule, department descriptions, program descriptions, course descriptions, school policies, student services, admissions, San diego Lifestyle, etc.
I will provide the text but I need a professional design with regard to page layouts. I have provided some examples.
Ok, i posted the catalog content, just missing course descriptions.
Target Market(s)
Young Professionals, Foreign Students
Industry/Entity Type
University
Look and feel
Each slider illustrates characteristics of the customer's brand and the style your logo design should communicate.

```html
<!DOCTYPE html>
<html lang="en">
<head>
<meta charset="utf-8">
<title>Table of Contents</title>
<link href="https://fonts.googleapis.com/css2?family=Carlito:wght@400;700&display=swap" rel="stylesheet">
<style>
  :root {
    --brand-blue: #2d6197;
    --rule-blue: #8fa9c8;
    --row-tint: #f3ecec;
    --row-plain: #f8f8fa;
    --ink: #222222;
    --muted: #8a8a8a;
    --paper: #ffffff;
  }
  * { margin: 0; padding: 0; box-sizing: border-box; }
  html, body { width: 927px; height: 1200px; overflow: hidden; background: var(--paper); }
  body { font-family: "Carlito", "Calibri", sans-serif; color: var(--ink); }
  .page { position: relative; width: 927px; height: 1200px; }

  .brand-name {
    position: absolute; left: 61px; top: 38px;
    display: flex; align-items: center; gap: 10px;
    font-size: 17px; color: var(--brand-blue); letter-spacing: 0.5px;
  }
  .brand-name .dot { width: 14px; height: 14px; border-radius: 50%; background: var(--brand-blue); }

  .header-rule { position: absolute; left: 0; top: 0; }
  .section-title {
    position: absolute; right: 24px; top: 104px;
    font-size: 33px; font-weight: 400; color: var(--paper); line-height: 38px;
  }

  .toc {
    position: absolute; left: 68px; top: 185px; width: 805px;
    border-collapse: collapse; font-size: 24px;
  }
  .toc th {
    background: var(--brand-blue); color: var(--paper); font-weight: 400;
    font-size: 26px; height: 36px; text-align: center;
  }
  .toc td { height: 36.3px; padding: 0 0 0 12px; line-height: 1; }
  .toc tr:nth-child(odd) td { background: var(--row-tint); }
  .toc tr:nth-child(even) td { background: var(--row-plain); }
  .toc .col-title { width: 660px; }
  .toc th.col-title { padding-right: 190px; }
  .toc td.col-page { text-align: center; padding: 0 10px 0 0; }
  .toc th.col-page { padding: 0; }
  .toc .spacer td { height: 24px; background: var(--row-plain); }

  .footer-rule { position: absolute; left: 0; top: 1154px; width: 927px; height: 2px; background: var(--rule-blue); }
  .page-footer {
    position: absolute; right: 38px; top: 1170px;
    font-size: 12px; color: var(--muted); letter-spacing: 0.3px;
  }
</style>
</head>
<body>
<div class="page">
  <div class="brand-name"><span class="dot"></span>Redwell Institute Bayshore</div>

  <svg class="header-rule" width="927" height="150" viewBox="0 0 927 150" aria-hidden="true">
    <rect x="0" y="100" width="927" height="2" fill="var(--brand-blue)"/>
    <polygon points="576,101 927,101 927,140 600,140" fill="var(--brand-blue)"/>
  </svg>
  <h1 class="section-title">TABLE OF CONTENTS</h1>

  <table class="toc">
    <thead>
      <tr><th class="col-title">CONTENTS</th><th class="col-page">PAGE NO.</th></tr>
    </thead>
    <tbody>
      <tr><td class="col-title">MISSION STATEMENT/ ACADEMIC OVERVIEW</td><td class="col-page">3</td></tr>
      <tr><td class="col-title">GENERAL INFORMATION</td><td class="col-page">4</td></tr>
      <tr><td class="col-title">ACADEMIC CALENDAR</td><td class="col-page">5</td></tr>
      <tr><td class="col-title">ACADEMIC PROGRAMS</td><td class="col-page">6</td></tr>
      <tr><td class="col-title">LANGUAGE ACQUISITION</td><td class="col-page">7</td></tr>
      <tr><td class="col-title">TESOL CERTIFICATE</td><td class="col-page">8</td></tr>
      <tr><td class="col-title">ACCOUNTING CERTIFICATE</td><td class="col-page">9</td></tr>
      <tr><td class="col-title">LEDGERLINE CERTIFICATE</td><td class="col-page">10</td></tr>
      <tr><td class="col-title">STARTING YOUR OWN BUSINESS CERTIFICATE</td><td class="col-page">11</td></tr>
      <tr><td class="col-title">MARKETING CERTIFICATE</td><td class="col-page">12</td></tr>
      <tr><td class="col-title">IMPORT/EXPORT BUSINESS CERTIFICATE</td><td class="col-page">13</td></tr>
      <tr><td class="col-title">E-COMMERCE/ONLINE MARKETING CERTIFICATE</td><td class="col-page">14</td></tr>
      <tr><td class="col-title">TAX AUDIT PREPARATION CERTIFICATE</td><td class="col-page">15</td></tr>
      <tr><td class="col-title">GRADUATE DEGREE (MBA)</td><td class="col-page">16</td></tr>
      <tr><td class="col-title">TRAVEL/STUDY PROGRAMS</td><td class="col-page">17</td></tr>
      <tr><td class="col-title">ONLINE LEARNING</td><td class="col-page">19</td></tr>
      <tr><td class="col-title">UNIVERSITY POLICIES</td><td class="col-page">20</td></tr>
      <tr><td class="col-title">ADMISSIONS</td><td class="col-page">22</td></tr>
      <tr><td class="col-title">GRADUATION REQUIREMENTS</td><td class="col-page">23</td></tr>
      <tr><td class="col-title">STUDENT SERVICES</td><td class="col-page">24</td></tr>
      <tr><td class="col-title">SAN DIEGO MAP</td><td class="col-page">25</td></tr>
      <tr><td class="col-title">SAN DIEGO LIFESTYLE</td><td class="col-page">26</td></tr>
      <tr><td class="col-title">FACULTY DESCRIPTIONS</td><td class="col-page">27</td></tr>
      <tr><td class="col-title">COURSE DESCRIPTIONS</td><td class="col-page">28</td></tr>
      <tr class="spacer"><td></td><td></td></tr>
    </tbody>
  </table>

  <div class="footer-rule"></div>
  <div class="page-footer">2::: REDWELL INSTITUTE</div>
</div>
</body>
</html>
```